Dalvick's Business Card

I need some designs for a new business card including the new logo attached. An old example of our business card is also attached to show all the data that should be included on the new design.
**I added some more examples someone had mocked up**

Contact Information for Business Card

Should include all info on other examples uploaded.

```html
<!DOCTYPE html>
<html lang="en">
<head>
<meta charset="utf-8">
<title>Dalvick's Business Card</title>
<link href="https://fonts.googleapis.com/css2?family=Montserrat:wght@400;600;700&display=swap" rel="stylesheet">
<style>
  :root {
    --backdrop: #ababab;
    --card-white: #ffffff;
    --brand-blue: #0f6fb8;
    --brand-red: #d3283a;
    --text-gray: #6b6b6b;
    --divider: #c9c9c9;
    --seal-gray: #e2e2e2;
  }
  html, body {
    margin: 0;
    padding: 0;
    width: 1200px;
    height: 1000px;
    overflow: hidden;
    background: var(--backdrop);
    font-family: "Montserrat", Arial, sans-serif;
  }
  .canvas {
    position: relative;
    width: 1200px;
    height: 1000px;
  }
  .card {
    position: absolute;
    left: 294px;
    width: 613px;
    height: 352px;
    border-radius: 28px;
    overflow: hidden;
  }
  .card-front {
    top: 94px;
    background: var(--card-white);
  }
  .card-back {
    top: 530px;
    background: linear-gradient(90deg, var(--brand-red) 0%, #8a4468 40%, #4f5690 65%, var(--brand-blue) 100%);
  }
  .brand-block {
    position: absolute;
    left: 40px;
    top: 140px;
    width: 250px;
    display: flex;
    align-items: center;
    justify-content: center;
    gap: 10px;
  }
  .brand-dot {
    width: 16px;
    height: 16px;
    border-radius: 50%;
    background: var(--brand-red);
  }
  .brand-name {
    font-weight: 700;
    font-size: 34px;
    color: var(--brand-blue);
    letter-spacing: 0.5px;
  }
  .divider {
    position: absolute;
    left: 288px;
    top: 108px;
    width: 1px;
    height: 144px;
    background: var(--divider);
  }
  .contact {
    position: absolute;
    left: 312px;
    top: 120px;
    color: var(--text-gray);
    font-size: 14.5px;
    letter-spacing: 0.3px;
  }
  .contact-name {
    margin: 0 0 12px;
    font-size: 18.5px;
    font-weight: 600;
    color: var(--brand-blue);
    letter-spacing: 0;
  }
  .contact-address {
    margin: 0 0 16px;
    line-height: 18px;
  }
  .contact-line {
    display: flex;
    align-items: center;
    gap: 5px;
    line-height: 18px;
  }
  .contact-line svg { flex: none; }
  .seal {
    position: absolute;
    left: 456px;
    top: 193px;
    width: 156px;
    height: 156px;
    border-radius: 50%;
    border: 3px solid var(--seal-gray);
    box-sizing: border-box;
  }
  .seal-inner {
    position: absolute;
    left: 34px;
    top: 34px;
    width: 82px;
    height: 82px;
    border-radius: 50%;
    background: var(--seal-gray);
  }
  .back-brand {
    position: absolute;
    left: 56px;
    top: 148px;
    display: flex;
    align-items: center;
    gap: 14px;
  }
  .back-dot {
    width: 22px;
    height: 22px;
    border-radius: 50%;
    background: var(--card-white);
  }
  .back-name {
    font-weight: 700;
    font-size: 46px;
    color: var(--card-white);
    letter-spacing: 0.5px;
  }
</style>
</head>
<body>
<div class="canvas">
  <section class="card card-front" aria-label="Card front">
    <div class="brand-block">
      <span class="brand-dot"></span>
      <span class="brand-name">DALVICK'S</span>
    </div>
    <div class="divider"></div>
    <div class="contact">
      <p class="contact-name">Reid Dalvick</p>
      <p class="contact-address">418 Maplecrest Avenue<br>Fairview, IA 51590, EUA</p>
      <div class="contact-line">
        <svg width="9" height="9" viewBox="0 0 10 10" aria-hidden="true"><path d="M2 0.5 L4 2.8 L3 4 Q4.5 6 6 7 L7.2 6 L9.5 8 L8 9.5 Q3 9 0.5 2 Z" fill="var(--brand-red)"/></svg>
        <span>712.555.0148</span>
      </div>
      <div class="contact-line">
        <svg width="10" height="8" viewBox="0 0 10 8" aria-hidden="true"><rect width="10" height="8" fill="var(--brand-red)"/><path d="M0 0 L5 4.5 L10 0" stroke="#fff" stroke-width="1" fill="none"/></svg>
        <span>hvacdalvick@mailbox.com</span>
      </div>
    </div>
    <div class="seal" role="img" aria-label="Licensed and insured, family owned seal">
      <div class="seal-inner"></div>
    </div>
  </section>

  <section class="card card-back" aria-label="Card back">
    <div class="back-brand">
      <span class="back-dot"></span>
      <span class="back-name">DALVICK'S</span>
    </div>
  </section>
</div>
</body>
</html>
```